ambitious event and festival agency from austria needs fresh business card design

A new design is due for the new headquarters and the new challenges. We organize events for different target groups from 16 to 60 years. The design should therefore be straightforward and not confused, so we are open to new colors and the logo may also be changed. In general, however, the most interesting suggestions are the most interesting ones. after this order we are looking for more graphics for brightloom facebook instagramm homepage etc A new design is due for the new headquarters and the new challenges. We organize events for different target groups from 16 to 60 years. The design should therefore be straightforward and not confused, so we are open to new colors and the logo may also be changed. In general, however, the most interesting suggestions are the most interesting ones. after this order we are looking for more graphics for brightloom facebook instagramm homepage etc A new design is due for the new headquarters and the new challenges. We organize events for different target groups from 16 to 60 years. The design should therefore be straightforward and not confused, so we are open to new colors and the logo may also be changed. In general, however, the most interesting suggestions are the most interesting ones. after this order we are looking for more graphics for brightloom facebook instagramm homepage etc
Updates

Reason: I am sorry for this decision but i need some more time. No new designs please, there are so many good ones and I will have made a decision in the next 3 days.

Target Market(s)

Industry/Entity Type

Business

Font styles to use
Serif
Sans Serif

Colors

Designer to choose colors to be used in the design.

Requirements
Must have
Nice to have
Should not have

```html
<!DOCTYPE html>
<html lang="de">
<head>
<meta charset="utf-8">
<title>brightloom – Visitenkarten</title>
<link rel="stylesheet" href="https://fonts.googleapis.com/css2?family=Lato:wght@400;700&display=swap">
<style>
  :root {
    --brand-red: #cf2f4a;
    --brand-red-dark: #b5243c;
    --band-grey: #8e9598;
    --paper: #f6f6f5;
    --ink-light: #f1f1f1;
    --backdrop: #e9e6e1;
  }
  * { box-sizing: border-box; margin: 0; padding: 0; }
  html, body {
    width: 1200px; height: 780px; overflow: hidden;
    background: var(--backdrop);
    font-family: "Lato", Arial, sans-serif;
  }
  .sheet {
    width: 1200px; height: 780px;
    display: flex; align-items: center; justify-content: center; gap: 40px;
  }
  .card {
    position: relative;
    width: 540px; height: 310px;
    overflow: hidden;
    box-shadow: 0 6px 18px rgba(0,0,0,.18);
  }

  /* Front side */
  .card-front { background: var(--paper); }
  .front-logo {
    position: absolute; left: 34px; top: 58px;
    font-size: 64px; font-weight: 700; letter-spacing: -1px;
    color: var(--brand-red);
  }
  .front-stripes { position: absolute; right: 0; top: 0; width: 540px; height: 310px; }
  .name-band {
    position: absolute; left: 0; top: 150px; width: 100%; height: 36px;
    background: var(--band-grey);
    display: flex; align-items: center; padding-left: 34px;
    color: #fff; font-size: 17px; letter-spacing: .2px;
  }
  .name-band .divider { margin: 0 10px; opacity: .85; }
  .contact-panel {
    position: absolute; left: 0; top: 186px; width: 100%; height: 124px;
    background: linear-gradient(180deg, var(--brand-red), var(--brand-red-dark));
    padding: 9px 34px 0;
    color: #fff;
  }
  .contact-list { list-style: none; font-size: 13.5px; line-height: 17.5px; }
  .contact-icons { display: flex; gap: 6px; margin-top: 5px; }
  .contact-icons svg { width: 18px; height: 18px; }

  /* Back side */
  .card-back {
    background: radial-gradient(ellipse at 40% 30%, #d8394f 0%, var(--brand-red) 45%, var(--brand-red-dark) 100%);
    display: flex; flex-direction: column; align-items: center; justify-content: center;
  }
  .back-logo {
    font-size: 68px; font-weight: 700; letter-spacing: -1px;
    color: var(--ink-light);
  }
  .back-url {
    margin-top: 14px;
    font-size: 14px; letter-spacing: 1px;
    color: var(--ink-light);
  }
</style>
</head>
<body>
<main class="sheet">

  <section class="card card-front" aria-label="Visitenkarte Vorderseite">
    <svg class="front-stripes" viewBox="0 0 540 310" aria-hidden="true">
      <polygon points="420,0 462,0 540,78 540,120" fill="var(--brand-red)"/>
      <polygon points="470,0 512,0 540,28 540,70" fill="var(--brand-red)"/>
    </svg>
    <div class="front-logo">brightloom</div>
    <div class="name-band">
      <span class="person-name">Lukas Berghammer</span>
      <span class="divider">|</span>
      <span class="person-role">Geschäftsführer</span>
    </div>
    <div class="contact-panel">
      <ul class="contact-list">
        <li>brightloom</li>
        <li>Talgasse 9, A4820 Ried</li>
        <li>+43 660 418 2375</li>
        <li>l.berghammer@brightloom.eu</li>
        <li>www.brightloom.eu</li>
      </ul>
      <div class="contact-icons" aria-hidden="true">
        <svg viewBox="0 0 18 18"><circle cx="9" cy="9" r="8" fill="none" stroke="#fff" stroke-width="1.3"/><rect x="6.3" y="4.5" width="5.4" height="9" rx="1" fill="#fff"/></svg>
        <svg viewBox="0 0 18 18"><circle cx="9" cy="9" r="8" fill="none" stroke="#fff" stroke-width="1.3"/><rect x="4.8" y="6" width="8.4" height="6" fill="#fff"/><polyline points="4.8,6 9,9.4 13.2,6" fill="none" stroke="var(--brand-red)" stroke-width="1"/></svg>
        <svg viewBox="0 0 18 18"><circle cx="9" cy="9" r="8" fill="none" stroke="#fff" stroke-width="1.3"/><circle cx="9" cy="9" r="4.5" fill="none" stroke="#fff" stroke-width="1.1"/><line x1="4.5" y1="9" x2="13.5" y2="9" stroke="#fff" stroke-width="1"/><ellipse cx="9" cy="9" rx="2" ry="4.5" fill="none" stroke="#fff" stroke-width="1"/></svg>
      </div>
    </div>
  </section>

  <section class="card card-back" aria-label="Visitenkarte Rückseite">
    <div class="back-logo">brightloom</div>
    <div class="back-url">www.brightloom.eu</div>
  </section>

</main>
</body>
</html>
```